Structural Engineering Business Card

Brookvane Drafting does residential house plans for clients in Central Florida. Would like simple but elegant business card that is appropriate for a house plan engineering company. Prefer black business card with black/white them but open to other shades of blue. I uploaded a sample card that I came across that looked good but please come up with your own creative designs.

Contact Information for Business Card

Name, Title, Phone, Email, Address, website

```html
<!DOCTYPE html>
<html lang="en">
<head>
<meta charset="utf-8">
<title>Brookvane Drafting – Business Card</title>
<link href="https://fonts.googleapis.com/css2?family=Poppins:wght@400;500;700;800&display=swap" rel="stylesheet">
<style>
  :root {
    --ink: #0b0b0b;
    --paper: #ffffff;
    --stage: #e9e9e9;
    --muted: #1c1c1c;
  }
  * { margin: 0; padding: 0; box-sizing: border-box; }
  html, body {
    width: 1200px; height: 900px; overflow: hidden;
    background: var(--stage);
    font-family: "Poppins", sans-serif;
  }
  .sheet {
    width: 1200px; height: 900px;
    display: flex; flex-direction: column; align-items: center; justify-content: center;
    gap: 40px;
  }
  .card {
    width: 680px; height: 388px; position: relative; overflow: hidden;
    box-shadow: 0 6px 18px rgba(0,0,0,.18);
  }
  /* Back side */
  .card--back { background: var(--ink); display: flex; align-items: center; justify-content: center; }
  .brand {
    display: flex; align-items: center; gap: 14px;
    font-weight: 800; text-transform: uppercase; letter-spacing: .5px; white-space: nowrap;
  }
  .brand__mark { width: 30px; height: 30px; background: currentColor; }
  .card--back .brand { color: var(--paper); font-size: 46px; }
  .card--back .brand__mark { width: 40px; height: 40px; }

  /* Front side */
  .card--front { background: var(--paper); color: var(--muted); }
  .card--front .brand { position: absolute; top: 62px; right: 44px; color: var(--ink); font-size: 22px; gap: 10px; }
  .card--front .brand__mark { width: 22px; height: 22px; }
  .person { position: absolute; left: 56px; top: 86px; }
  .person__name { font-weight: 700; font-size: 24px; color: var(--ink); letter-spacing: .5px; line-height: 1.1; }
  .person__title { font-weight: 400; font-size: 15px; color: var(--muted); margin-top: 2px; letter-spacing: .4px; }
  .contact { position: absolute; left: 72px; top: 188px; font-size: 16px; line-height: 1.45; letter-spacing: .3px; }
  .contact__row { display: flex; align-items: center; gap: 10px; }
  .contact__icon { width: 18px; height: 18px; fill: var(--ink); }
  .contact__address { margin-top: 14px; padding-left: 2px; }
  .wave { position: absolute; inset: 0; }
  .site { position: absolute; right: 40px; bottom: 42px; color: var(--paper); font-size: 15px; letter-spacing: .5px; }
</style>
</head>
<body>
<main class="sheet">
  <section class="card card--back" aria-label="Card back">
    <div class="brand"><span class="brand__mark"></span>Brookvane Drafting</div>
  </section>

  <section class="card card--front" aria-label="Card front">
    <svg class="wave" viewBox="0 0 680 388" preserveAspectRatio="none" aria-hidden="true">
      <path d="M0,322 C210,326 430,262 680,140 L680,388 L0,388 Z" fill="var(--ink)"/>
      <path d="M0,352 C190,350 380,300 520,214" fill="none" stroke="var(--paper)" stroke-width="3"/>
    </svg>

    <div class="brand"><span class="brand__mark"></span>Brookvane Drafting</div>

    <div class="person">
      <div class="person__name">DANIEL HARROW</div>
      <div class="person__title">Managing Director</div>
    </div>

    <div class="contact">
      <div class="contact__row">
        <svg class="contact__icon" viewBox="0 0 24 24"><path d="M6.6 10.8a15.5 15.5 0 0 0 6.6 6.6l2.2-2.2a1 1 0 0 1 1-.25 11.4 11.4 0 0 0 3.6.57 1 1 0 0 1 1 1V20a1 1 0 0 1-1 1A17 17 0 0 1 3 4a1 1 0 0 1 1-1h3.5a1 1 0 0 1 1 1c0 1.25.2 2.45.57 3.57a1 1 0 0 1-.25 1z"/></svg>
        <span>407-555 0142</span>
      </div>
      <div class="contact__row">
        <svg class="contact__icon" viewBox="0 0 24 24"><path d="M2 5h20v14H2z M3.5 6.5 12 13l8.5-6.5" fill="none" stroke="var(--ink)" stroke-width="2"/></svg>
        <span>hello@brookvane.com</span>
      </div>
      <div class="contact__address">218 Cypress Lane<br>Orlando, FL 32801</div>
    </div>

    <div class="site">www.brookvane.com</div>
  </section>
</main>
</body>
</html>
```